New Business Card Design Project

Need a design that will create an impact / strong impression towards our clients for our business. We are in the lighting business and we do lighting retrofits for large commercial to industrial clientele.

Target Market(s)

Lighting Industry

Industry/Entity Type

Business

Font styles to use
Other font styles liked:
• we would like to use the font on our logo, not sure what it is though..

Requirements
Must have
• Our logo.
Nice to have
• We are open to suggestions that have to do with lighting.

```html
<!DOCTYPE html>
<html lang="en">
<head>
<meta charset="utf-8">
<title>Summit Lumen Works – Business Card</title>
<link href="https://fonts.googleapis.com/css2?family=Roboto:wght@400;500;700&family=Roboto+Condensed:wght@400;500&display=swap" rel="stylesheet">
<style>
  :root {
    --backdrop: #5b4a3a;
    --paper: #f2f2f2;
    --forest: #10360f;
    --green-mid: #0b7a35;
    --green-light: #62c257;
    --ink: #4a4a4a;
    --white: #ffffff;
  }
  * { margin: 0; padding: 0; box-sizing: border-box; }
  html, body { width: 1200px; height: 960px; overflow: hidden; }
  body {
    position: relative;
    background: var(--backdrop);
    font-family: "Roboto", Arial, sans-serif;
  }
  .card {
    position: absolute;
    width: 600px;
    height: 343px;
    box-shadow: 2px 3px 4px rgba(0,0,0,0.35);
  }
  .card-front { left: 314px; top: 113px; background: var(--paper); }
  .card-back  { left: 312px; top: 472px; background: var(--forest); }

  .brand {
    position: absolute;
    left: 41px;
    top: 58px;
    display: flex;
    align-items: center;
    gap: 10px;
  }
  .brand-square { width: 20px; height: 20px; background: var(--green-mid); }
  .brand-name {
    font-weight: 700;
    font-size: 22px;
    color: var(--green-mid);
    letter-spacing: 0.5px;
  }

  .address {
    position: absolute;
    left: 41px;
    top: 167px;
    font-size: 14px;
    line-height: 18px;
    color: var(--ink);
  }
  .contacts {
    position: absolute;
    left: 41px;
    top: 214px;
    list-style: none;
    font-size: 14px;
    line-height: 19px;
    color: var(--ink);
  }
  .contacts li { display: flex; align-items: center; gap: 9px; }
  .contacts svg { width: 14px; height: 14px; fill: var(--forest); flex: none; }

  .name-band {
    position: absolute;
    left: 336px;
    top: 204px;
    width: 264px;
    height: 69px;
  }
  .name-band svg { position: absolute; inset: 0; }
  .name-block {
    position: absolute;
    right: 34px;
    top: 10px;
    text-align: right;
    color: var(--white);
    font-family: "Roboto Condensed", Arial, sans-serif;
  }
  .person-name { font-size: 23px; font-weight: 500; line-height: 26px; }
  .person-role { font-size: 15px; line-height: 20px; }

  .back-brand {
    position: absolute;
    left: 0;
    right: 0;
    top: 140px;
    display: flex;
    justify-content: center;
    align-items: center;
    gap: 14px;
  }
  .back-brand .brand-square { width: 30px; height: 30px; background: var(--green-light); }
  .back-brand .brand-name { font-size: 34px; color: var(--white); }
  .back-url {
    position: absolute;
    left: 0;
    right: 0;
    top: 281px;
    text-align: center;
    font-size: 14px;
    letter-spacing: 3px;
    color: var(--white);
  }
</style>
</head>
<body>

<section class="card card-front">
  <div class="brand">
    <span class="brand-square"></span>
    <span class="brand-name">SUMMIT LUMEN WORKS, LLC.</span>
  </div>

  <p class="address">1420 Cedar Ridge Road<br>Fairbanks, Alaska 99701</p>

  <ul class="contacts">
    <li>
      <svg viewBox="0 0 16 16" aria-hidden="true"><path d="M3.6 1.2l2.3 2.6-1.3 1.8c.9 2 2.7 3.8 4.8 4.8l1.8-1.3 2.6 2.3-1.2 2.6C7.4 14 2 8.6 1 2.4z"/></svg>
      907 555 0142
    </li>
    <li>
      <svg viewBox="0 0 16 16" aria-hidden="true"><path d="M4.5 0h7a1 1 0 0 1 1 1v14a1 1 0 0 1-1 1h-7a1 1 0 0 1-1-1V1a1 1 0 0 1 1-1zm.6 2v10.5h5.8V2zM8 13.3a.9.9 0 1 0 0 1.8.9.9 0 0 0 0-1.8z"/></svg>
      907 555 0187
    </li>
    <li>
      <svg viewBox="0 0 16 16" aria-hidden="true"><path d="M4 1h8v4H4zM1 6h14v6h-2v3H3v-3H1zm3.5 4v3.5h7V10z"/></svg>
      907 555 0163
    </li>
    <li>
      <svg viewBox="0 0 16 16" aria-hidden="true"><path d="M1 3h14v10H1zm1.6 1.4v.4L8 8.6l5.4-3.8v-.4z"/></svg>
      daniel@summitlumen.com
    </li>
    <li>
      <svg viewBox="0 0 16 16" aria-hidden="true"><circle cx="8" cy="8" r="7"/><path d="M5 4.5c1.5 0 2 1.2 1.5 2.3-.6 1 .4 1.7 1.5 1.4M10 12c-.4-1.4.4-2.4 1.8-2.3" stroke="#f2f2f2" stroke-width="1.4" fill="none"/></svg>
      www.summitlumen.com
    </li>
  </ul>

  <div class="name-band">
    <svg viewBox="0 0 264 69" aria-hidden="true">
      <polygon points="0,69 13,69 70,0 57,0" fill="#62c257"/>
      <polygon points="15,69 21,69 78,0 72,0" fill="#0b7a35"/>
      <polygon points="23,69 264,69 264,0 80,0" fill="#10360f"/>
    </svg>
    <div class="name-block">
      <div class="person-name">DANIEL REYES</div>
      <div class="person-role">CEO/FOUNDER</div>
    </div>
  </div>
</section>

<section class="card card-back">
  <div class="back-brand">
    <span class="brand-square"></span>
    <span class="brand-name">SUMMIT LUMEN</span>
  </div>
  <p class="back-url">www.summitlumenworks.com</p>
</section>

</body>
</html>
```